NEW Modern Sleek Business Card for VR Language Startup

Our startup is using VR to lead the next wave of world language education. We need a two-sided business card that introduces the larger organization (Brightloom Language Inc) and our contact info on one side and shows the product, Glimwoorld, on the other side.

Side 1 (contact info)= Brightloom Logo and Contact info (name, title, phone, email)

Side 2 (product)= Glimworld logo, text, and website
Text= Culturally Immersive Language Learning Games
Website= www.glimworld-play.com

Target Market(s)

Education, Technology

Contact Information for Business Card

Contact info will be updated upon approval of the design. For now, put this as a placeholder.

Perry Dunmore
Founder & CEO
pdunmore@quillpost-mail.net
(555)-014-2286

Font styles to use
Other font styles liked:
• Gibson and Century Gothic are the brand fonts

Requirements
Nice to have
• I would love to see cohesion between the design and colors of the two logos. I have attached a few business card designs that I like, so you can get a feel for my preferred style.

```html
<!DOCTYPE html>
<html lang="en">
<head>
<meta charset="utf-8">
<title>Brightloom Language – Business Card</title>
<link href="https://fonts.googleapis.com/css2?family=Montserrat:wght@600&family=Questrial&display=swap" rel="stylesheet">
<style>
  :root {
    --backdrop: #c5c8cb;
    --card: #212121;
    --card-shade: #2a2a2a;
    --ink: #f2f2f2;
    --accent-blue: #3ab5e6;
    --accent-pink: #e8457a;
  }
  * { box-sizing: border-box; margin: 0; padding: 0; }
  html, body {
    width: 1200px; height: 900px; overflow: hidden;
    background: var(--backdrop);
  }
  .sheet { position: relative; width: 1200px; height: 900px; }
  .card {
    position: absolute; top: 279px;
    width: 474px; height: 273px;
    background: var(--card);
    overflow: hidden;
    font-family: "Questrial", "Century Gothic", sans-serif;
    color: var(--ink);
  }
  .card--contact { left: 109px; }
  .card--product { left: 613px; }

  .backdrop-art {
    position: absolute;
    background: var(--card-shade);
  }
  .card--contact .backdrop-art {
    left: 330px; top: -20px; width: 190px; height: 300px;
    border-radius: 45% 20% 10% 60% / 30% 20% 20% 60%;
  }
  .card--product .backdrop-art {
    left: -70px; top: 20px; width: 190px; height: 250px;
    border-radius: 30% 50% 40% 20% / 25% 35% 45% 20%;
  }

  .brand {
    position: absolute;
    display: flex; align-items: center; gap: 10px;
  }
  .brand__dot {
    border-radius: 50%;
    background: var(--accent-pink);
    flex: none;
  }
  .brand__name {
    font-family: "Montserrat", "Century Gothic", sans-serif;
    font-weight: 600;
    letter-spacing: 0.12em;
    color: var(--ink);
    text-transform: uppercase;
    white-space: nowrap;
  }
  .card--contact .brand { left: 32px; top: 56px; }
  .card--contact .brand__dot { width: 44px; height: 44px; }
  .card--contact .brand__name { font-size: 20px; }
  .card--product .brand { left: 212px; top: 76px; }
  .card--product .brand__dot { width: 58px; height: 58px; }
  .card--product .brand__name { font-size: 21px; letter-spacing: 0.1em; }

  .person { position: absolute; left: 32px; top: 143px; }
  .person__name {
    font-family: "Montserrat", "Century Gothic", sans-serif;
    font-weight: 600; font-size: 15px; letter-spacing: 0.08em;
    color: var(--accent-blue); text-transform: uppercase;
  }
  .person__title { font-size: 12px; margin-top: 4px; }

  .contact-list { position: absolute; left: 31px; top: 199px; list-style: none; }
  .contact-list li {
    display: flex; align-items: center; gap: 8px;
    font-size: 12px; height: 20px;
  }
  .contact-list svg, .product-site svg { width: 9px; height: 9px; flex: none; }

  .product-site {
    position: absolute; left: 0; right: 0; top: 208px;
    padding-left: 130px;
    display: flex; align-items: center; justify-content: center; gap: 6px;
    font-size: 12px;
  }
  .product-tagline {
    position: absolute; left: 130px; right: 0; top: 230px;
    text-align: center; font-size: 12px;
  }
</style>
</head>
<body>
<main class="sheet">
  <section class="card card--contact">
    <div class="backdrop-art" role="img" aria-label="Faint large brand symbol decoration"></div>
    <div class="brand">
      <span class="brand__dot"></span>
      <span class="brand__name">Brightloom</span>
    </div>
    <div class="person">
      <p class="person__name">Perry Dunmore</p>
      <p class="person__title">Founder &amp; CEO</p>
    </div>
    <ul class="contact-list">
      <li>
        <svg viewBox="0 0 10 10" aria-hidden="true"><path fill="var(--accent-blue)" d="M2 0.5 L3.8 2.6 L2.8 3.7 Q4 6 6.3 7.2 L7.4 6.2 L9.5 8 L8.2 9.5 Q4.5 9.3 2.2 6.8 Q0.6 4.8 0.5 1.8 Z"/></svg>
        (555)-014-2286
      </li>
      <li>
        <svg viewBox="0 0 10 10" aria-hidden="true"><rect x="0.5" y="1.5" width="9" height="7" fill="var(--accent-blue)"/><path d="M1 2.2 L5 5.5 L9 2.2" stroke="var(--card)" stroke-width="0.9" fill="none"/></svg>
        pdunmore@quillpost-mail.net
      </li>
    </ul>
  </section>

  <section class="card card--product">
    <div class="backdrop-art" role="img" aria-label="Faint large product symbol decoration"></div>
    <div class="brand">
      <span class="brand__dot"></span>
      <span class="brand__name">Glimworld</span>
    </div>
    <p class="product-site">
      <svg viewBox="0 0 10 10" aria-hidden="true"><circle cx="5" cy="5" r="4.5" fill="var(--accent-blue)"/><path d="M5 0.5 V9.5 M0.5 5 H9.5" stroke="var(--card)" stroke-width="0.7"/></svg>
      www.glimworld-play.com
    </p>
    <p class="product-tagline">Culturally Immersive Language Learning Games</p>
  </section>
</main>
</body>
</html>
```